New template needed for Joomla 3.2 website

We are a mortgage origination company based in Johannesburg, South Africa and require a sleek, modern & professional look for our website.
The website is complete and your template should accommodate all pages on the site (there are not many) and be ready for Joomla implementation.
Our website can be viewed at www.keystonebondhub.co.za
Target Market(s)
We are targeting consumers who require mortgage finance to buy real estate. There is no particular demographic, except that we cater to South African home buyers exclusively!
Requirements
Must have
- It must look professional and modern.
Take a look at competitor websites:
www.ziva.co.za
www.pkbondfinder.com
http://www.tallwavegroup.co.za/bondpeak/
http://www.ridgeloan.co.za/
We want to beat the competition !!
Nice to have
- Website should blend with company logo and play on the symbol in the logo.
I want more of a people / photo element to the template. It needs to make us seem "tangible"

```html
<!DOCTYPE html>
<html lang="en">
<head>
<meta charset="utf-8">
<title>Keystone Bond Hub</title>
<link href="https://fonts.googleapis.com/css2?family=PT+Sans:wght@400;700&display=swap" rel="stylesheet">
<style>
:root{
  --blue:#0a78b4;
  --text:#666;
  --heading:#0a6fa9;
  --band:#f1f1f1;
  --border:#e1e1e1;
  --footer:#3d3d3d;
  --footer-text:#cfcfcf;
}
*{box-sizing:border-box;margin:0;padding:0}
html,body{width:779px;height:1200px;overflow:hidden;background:#fff}
body{position:relative;font-family:"PT Sans",sans-serif;color:var(--text)}
.abs{position:absolute}
/* header */
.site-name{left:85px;top:20px;font-size:20px;font-weight:400;color:var(--heading);line-height:24px}
.call{right:85px;top:15px;display:flex;gap:8px;align-items:center}
.call-label{font-size:9px;color:#444}
.call-number{font-size:12.5px;font-weight:700;color:var(--blue)}
/* nav */
.nav{left:85px;top:65px;width:609px;height:32px;display:flex;background:linear-gradient(#1a8fcf,#0a6ea8)}
.nav a{display:flex;align-items:center;justify-content:center;color:#fff;font-size:9.5px;text-decoration:none;border-right:1px solid rgba(0,0,0,.15)}
/* hero */
.hero{left:0;top:97px;width:779px;height:281px;background:linear-gradient(90deg,#b9b6ae 0%,#d7d5cf 45%,#c8c6c0 100%)}
.hero-title{right:85px;top:146px;text-align:right;color:#fff;font-weight:700;font-size:27px;line-height:39px}
.hero-text{right:85px;top:234px;width:260px;text-align:right;color:#fff;font-size:10.5px;line-height:18px}
.dots{left:629px;top:305px;width:64px;height:19px;background:rgba(255,255,255,.35);border-radius:2px;display:flex;gap:4px;align-items:center;justify-content:center}
.dots span{width:9px;height:9px;border-radius:50%;background:rgba(255,255,255,.6)}
.dots span:first-child{background:#fff}
/* feature cards */
.feature{top:424px;width:194px;height:154px;border:1px solid var(--border);background:linear-gradient(#f2f2f2,#fff 70%)}
.feature-icon{position:absolute;left:11px;top:12px;width:46px;height:46px;border-radius:50%;background:#9a9a9a}
.feature-title{position:absolute;left:68px;top:14px;font-size:16px;line-height:21px;color:var(--heading)}
.feature p{position:absolute;left:11px;right:10px;top:70px;font-size:8.5px;line-height:14.5px}
.btn{display:inline-flex;align-items:center;justify-content:center;width:63px;height:19px;background:var(--blue);color:#fff;font-size:8.5px;text-decoration:none;border-radius:1px}
.feature .btn{position:absolute;left:11px;top:123px}
/* band */
.band{left:0;top:612px;width:779px;height:288px;background:var(--band)}
.promo-photo{top:646px;width:251px;height:122px}
.promo-title{top:788px;width:300px;text-align:center;font-size:15px;color:var(--heading);font-weight:400}
.promo-text{top:822px;width:300px;text-align:center;font-size:8px;line-height:15.5px}
/* action cards */
.action{top:944px;width:142px;height:134px;border:1px solid #dcdcdc;background:#fff;text-align:center}
.action-head{position:absolute;left:10px;top:10px;display:flex;align-items:center;gap:8px;font-size:12.5px;color:var(--heading)}
.action p{position:absolute;left:8px;right:8px;top:43px;font-size:8px;line-height:15.8px}
.action .btn{position:absolute;left:39px;top:99px}
/* footer */
.footer{left:0;top:1122px;width:779px;height:78px;background:var(--footer)}
.footer-links{left:86px;top:1140px;font-size:8.5px;color:var(--footer-text);line-height:15.7px}
.footer-links span{margin:0 6px}
.top-btn{left:649px;top:1144px;width:38px;height:38px;background:#5a5a5a;color:#fff;font-size:9px;display:flex;flex-direction:column;align-items:center;justify-content:center;line-height:8px}
</style>
</head>
<body>
<header>
  <div class="abs site-name">Keystone Bond Hub</div>
  <div class="abs call">
    <svg width="26" height="26" viewBox="0 0 26 26"><circle cx="13" cy="13" r="12" fill="none" stroke="#bbb" stroke-width="1.2"/><path d="M9 7c-2 2-1 7 3 11s7 4 8 2l-2-3-2 1c-2-1-4-3-5-5l1-2-3-4z" fill="none" stroke="#999" stroke-width="1.2"/></svg>
    <div>
      <div class="call-label">Call Us Now</div>
      <div class="call-number">(010) 555 0148</div>
    </div>
  </div>
  <nav class="abs nav">
    <a href="#" style="width:58px">Home</a>
    <a href="#" style="width:83px">About Keystone</a>
    <a href="#" style="width:126px">Important Information</a>
    <a href="#" style="width:125px">Homeloan Calculators</a>
    <a href="#" style="width:95px">Apply On-Line</a>
    <a href="#" style="width:122px;border-right:0">Contact Keystone</a>
  </nav>
</header>

<section>
  <div class="abs hero" role="img" aria-label="Photo of a hand holding a small model house"></div>
  <h1 class="abs hero-title">FAST HOMELOANS<br>GREAT SERVICE !</h1>
  <p class="abs hero-text">Keystone Bond Hub intimately understands the need for first class customer service, coupled with an easy finance application process.</p>
  <div class="abs dots"><span></span><span></span><span></span><span></span></div>
</section>

<section>
  <div class="abs feature" style="left:85px">
    <div class="feature-icon"></div>
    <div class="feature-title">100%<br>Free of Charge</div>
    <p>No hidden costs or service charges. Our fee is not hidden within the finance charges of your homeloan.</p>
    <a class="btn" href="#">Learn More</a>
  </div>
  <div class="abs feature" style="left:293px">
    <div class="feature-icon"></div>
    <div class="feature-title">Exceptional<br>Service</div>
    <p>We guarantee a first class service to you. Our home loan specialists are up to date with the latest finance criteria.</p>
    <a class="btn" href="#">Learn More</a>
  </div>
  <div class="abs feature" style="left:500px">
    <div class="feature-icon" role="img" aria-label="Credit magnifier icon" style="background:#8c8c8c"></div>
    <div class="feature-title" style="left:91px;top:24px">Credit Help</div>
    <p>Problems with your credit record? We will do our best to help you into the clear with sound advice.</p>
    <a class="btn" href="#">Learn More</a>
  </div>
</section>

<section>
  <div class="abs band"></div>
  <div class="abs promo-photo" style="left:106px;background:linear-gradient(90deg,#d8d6d1,#bdbbb6)" role="img" aria-label="Photo of business people holding a referral program banner"></div>
  <div class="abs promo-photo" style="left:419px;background:linear-gradient(135deg,#6e7e86,#8fb3c2 50%,#c99c86)" role="img" aria-label="Photo of a hand holding a payment card"></div>
  <h2 class="abs promo-title" style="left:84px">Keystone Lead Referral Program</h2>
  <h2 class="abs promo-title" style="left:394px;top:790px">Keystone PayLink Card</h2>
  <p class="abs promo-text" style="left:84px">We invite members of the public, estate agents, attorneys, property developers and all other property professionals to refer leads to us. Why not join our referal program and earn money for every successful lead. It pays!</p>
  <p class="abs promo-text" style="left:394px">All members of our lead referal program will receive a Keystone Bond Hub PayLink card. We will load money earned from referals to your card and for you to spend in any way you please! These cards are accepted.</p>
</section>

<section>
  <div class="abs action" style="left:85px">
    <div class="action-head"><svg width="18" height="16" viewBox="0 0 18 16"><rect x="1" y="2" width="14" height="10" fill="none" stroke="#555" stroke-width="1.5"/><path d="M4 7l3 3 8-8" fill="none" stroke="#555" stroke-width="2"/><rect x="0" y="13" width="17" height="2" fill="#555"/></svg>Referral Program</div>
    <p>Click on the button below to join our lead referal program and start earning money.</p>
    <a class="btn" href="#">Join Today</a>
  </div>
  <div class="abs action" style="left:241px">
    <div class="action-head"><svg width="16" height="17" viewBox="0 0 16 17"><circle cx="8" cy="5" r="4" fill="#555"/><path d="M0 17c0-6 4-7 8-7s8 1 8 7z" fill="#555"/></svg>Get Pre Qualified</div>
    <p>Our experienced consultants would be happy to prequalify you for a homeloan.</p>
    <a class="btn" href="#">Apply Now</a>
  </div>
  <div class="abs action" style="left:396px">
    <div class="action-head"><svg width="18" height="18" viewBox="0 0 18 18"><circle cx="9" cy="9" r="8" fill="none" stroke="#555" stroke-width="1.3"/><path d="M6.5 7a2.5 2.5 0 1 1 3.5 2.3c-.8.4-1 .9-1 1.7" fill="none" stroke="#555" stroke-width="1.4"/><circle cx="9" cy="13.5" r="1" fill="#555"/></svg>Ask a Question</div>
    <p>Ask an experienced consultant to answer all your questions about homeloan finance.</p>
    <a class="btn" href="#" style="top:100px">Ask Now</a>
  </div>
  <div class="abs action" style="left:552px">
    <div class="action-head"><svg width="16" height="20" viewBox="0 0 16 20"><rect x="1" y="1" width="14" height="18" fill="none" stroke="#555" stroke-width="1.4"/><rect x="3.5" y="3.5" width="9" height="3" fill="#555"/><g fill="#555"><rect x="3.5" y="9" width="2" height="2"/><rect x="7" y="9" width="2" height="2"/><rect x="10.5" y="9" width="2" height="2"/><rect x="3.5" y="12.5" width="2" height="2"/><rect x="7" y="12.5" width="2" height="2"/><rect x="10.5" y="12.5" width="2" height="2"/><rect x="3.5" y="16" width="2" height="1.5"/><rect x="7" y="16" width="2" height="1.5"/><rect x="10.5" y="16" width="2" height="1.5"/></g></svg>Calculators</div>
    <p>Find out what you can afford with our convenient finance calculators.</p>
    <a class="btn" href="#" style="top:100px">Calculate</a>
  </div>
</section>

<footer>
  <div class="abs footer"></div>
  <div class="abs footer-links">
    <div>Privacy Policy<span>|</span>About Keystone<span>|</span>Contact Keystone</div>
    <div>Built with HTML5 and CSS3</div>
    <div>Copyright © 2014 Keystone Bond Hub (Pty) Ltd</div>
  </div>
  <div class="abs top-btn"><span>↑</span><span>TOP</span></div>
</footer>
</body>
</html>
```